Emerging automotive detailing business

I am starting a small automotive detailing business in hopes of becoming a well-known detailer to work on high end cars. I would like a card to reflect the high quality and time I put into my work. The name of the company is Bright Crest Detailing. I feel like it represents racecars getting off the line at the drag strip as well as an innuendo of "Up the Ladder". I do minor paint correction such as clay barring, multi-step buffing and polishing, waxing, hand washes, etc. I am always striving to learn more and improve my work. My goal is to have total customer satisfaction. This is a female run business but I do not want it to be very girly. Elegant is okay! I have pictures of my personal wrenfield attached, they do not need to be incorporated but if you can think of a cool way to use 1 or all of them, go for it!

Target Market(s)

Anyone that owns a vehicle. Preferably high end vehicles such as Valtori, Castellverde and Morvani but I will also happily work on any car, truck or suv no matter what brand.

Industry/Entity Type

Automotive

Contact Information for Business Card

Bright Crest Detailing
Mira Tolland
4175 Quenhollow Rd
Ashmere PA 17492
Cell phone- call/text- 717-555-0148
email- brightcrestdetails@maildrop-example.com
Instagram: @brightcrestdetailing
Facebook: facebook.com/brightcrestdetailing

Requirements
Must have
• Business name, my name, address, phone number. Listing that I do minor paint correction such as clay barring, multi-step buffing and polishing, waxing, hand washes, interior cleaning, and more. (This last part was in nice to haves but I have realized that I do really want it, so I moved it to must haves.) I want something that is different and eye-catching to my customers. Some people have done this very well with cards already submitted to me, but a lot have not. I didn't mess with the "look and feel bars" much because because I am pretty open to the overall design as long as it is not your basic run of the mill design.
Nice to have
• Something car related. Maybe an appointment time/date line. I do not have a logo, but if you would like to design one and incorporate it, that would be amazing!
Should not have
• Purple and Pink colors. Boring, basic, normal card.

```html
<!DOCTYPE html>
<html lang="en">
<head>
<meta charset="utf-8">
<title>Bright Crest Detailing – Business Card</title>
<link rel="stylesheet" href="https://fonts.googleapis.com/css2?family=Poiret+One&family=Didact+Gothic&display=swap">
<style>
  :root {
    --backdrop: #f3ea1e;
    --ink: #111111;
    --band: #050505;
    --silver-light: #f1f1f1;
    --silver-mid: #c9c9c9;
    --silver-dark: #7d7d7d;
    --stripe: #9a9a9a;
  }
  * { margin: 0; padding: 0; box-sizing: border-box; }
  html, body { width: 1200px; height: 800px; overflow: hidden; }
  body {
    background: var(--backdrop);
    font-family: "Didact Gothic", sans-serif;
    color: var(--ink);
    position: relative;
  }
  .card {
    position: absolute;
    top: 284px;
    width: 430px;
    height: 238px;
    overflow: hidden;
    background:
      radial-gradient(ellipse 70% 45% at 50% 55%, var(--silver-light) 0%, rgba(241,241,241,0) 100%),
      linear-gradient(180deg, var(--silver-dark) 0%, var(--silver-mid) 30%, var(--silver-light) 55%, var(--silver-mid) 80%, var(--silver-dark) 100%);
  }
  .card--front { left: 110px; }
  .card--back { left: 638px; }
  .card__wave { position: absolute; left: 0; top: 0; width: 430px; height: 238px; }

  .brand {
    position: absolute;
    left: 6px; width: 222px; top: 62px;
    font-family: "Poiret One", sans-serif;
    font-size: 29px;
    line-height: 37px;
    text-align: center;
    letter-spacing: 0.5px;
    text-transform: uppercase;
  }
  .divider {
    position: absolute;
    left: 229px; top: 32px;
    width: 1px; height: 150px;
    background: linear-gradient(180deg, rgba(60,60,60,0), #555 20%, #555 80%, rgba(60,60,60,0));
  }
  .contact { position: absolute; left: 244px; top: 44px; font-size: 11px; line-height: 14px; }
  .contact__name { font-size: 14px; margin-bottom: 7px; }
  .contact__address { margin-bottom: 6px; }
  .contact__row { display: flex; align-items: center; gap: 3px; white-space: nowrap; }
  .contact__row--email { font-size: 9.6px; }
  .icon { width: 10px; height: 10px; flex: none; }

  .services {
    position: absolute;
    left: 0; width: 430px; top: 60px;
    text-align: center;
    font-size: 12.5px;
    line-height: 16px;
    text-transform: uppercase;
    letter-spacing: 0.2px;
  }
  .rule {
    position: absolute;
    left: 135px; top: 131px;
    width: 160px; height: 2px;
    background: linear-gradient(90deg, rgba(40,40,40,0), #333 30%, #333 70%, rgba(40,40,40,0));
  }
  .appointment { position: absolute; left: 27px; top: 154px; font-size: 11px; display: flex; align-items: center; gap: 4px; }
  .appointment__field { position: absolute; top: 178px; font-size: 11px; }
  .appointment__field--time { left: 43px; }
  .appointment__field--date { left: 200px; }
</style>
</head>
<body>

<section class="card card--front" aria-label="Business card front">
  <svg class="card__wave" viewBox="0 0 430 238" aria-hidden="true">
    <path d="M0 176 Q140 232 430 208 L430 238 L0 238 Z" fill="var(--band)"/>
    <path d="M0 182 Q140 236 430 212" fill="none" stroke="var(--stripe)" stroke-width="2"/>
  </svg>

  <h1 class="brand">Bright Crest<br>Detailing</h1>
  <div class="divider"></div>

  <div class="contact">
    <p class="contact__name">Mira Tolland</p>
    <p class="contact__address">4175 Quenhollow Rd<br>Ashmere, PA 17492</p>
    <p class="contact__row">
      <svg class="icon" viewBox="0 0 10 10" aria-hidden="true"><rect x="2.5" y="0.5" width="5" height="9" rx="1" fill="none" stroke="var(--ink)"/><rect x="4" y="7.5" width="2" height="0.8" fill="var(--ink)"/></svg>
      (717) 555-0148
    </p>
    <p class="contact__row contact__row--email">
      <svg class="icon" viewBox="0 0 10 10" aria-hidden="true"><rect x="0.5" y="2" width="9" height="6" fill="none" stroke="var(--ink)"/><path d="M0.5 2 L5 5.5 L9.5 2" fill="none" stroke="var(--ink)"/></svg>
      brightcrestdetails@maildrop-example.com
    </p>
    <p class="contact__row">
      <svg class="icon" viewBox="0 0 10 10" aria-hidden="true"><rect x="0.5" y="0.5" width="9" height="9" rx="1.5" fill="var(--ink)"/></svg>
      @brightcrestdetailing
    </p>
    <p class="contact__row">
      <svg class="icon" viewBox="0 0 10 10" aria-hidden="true"><rect x="0.5" y="0.5" width="9" height="9" rx="1.5" fill="var(--ink)"/></svg>
      @brightcrestdetailing
    </p>
  </div>
</section>

<section class="card card--back" aria-label="Business card back">
  <svg class="card__wave" viewBox="0 0 430 238" aria-hidden="true">
    <path d="M0 0 L430 0 L430 30 Q220 10 0 66 Z" fill="var(--band)"/>
    <path d="M0 70 Q220 14 430 34" fill="none" stroke="var(--stripe)" stroke-width="2"/>
  </svg>

  <p class="services">Minor paint correction;<br>claying, multi-step buffing and polishing,<br>waxing, hand washes, interior cleaning and more!</p>
  <div class="rule"></div>

  <p class="appointment">
    <svg class="icon" viewBox="0 0 12 12" aria-hidden="true" style="width:13px;height:13px"><rect x="0.7" y="1.5" width="10.6" height="9.8" fill="none" stroke="var(--ink)" stroke-width="1.2"/><rect x="0.7" y="1.5" width="10.6" height="2.5" fill="var(--ink)"/><path d="M4 6 H8 L5.5 10" fill="none" stroke="var(--ink)" stroke-width="1"/></svg>
    Your next appointment:
  </p>
  <p class="appointment__field appointment__field--time">Time:</p>
  <p class="appointment__field appointment__field--date">Date:</p>
</section>

</body>
</html>
```